Now Leasing Banner

Looking for a banner that says the following information approx 4' x 30'

Now Leasing Maplebrook Terrace 925-318-6042

Target Market(s)

Drive by traffic

Industry/Entity Type

Residential property management

Requirements
Must have
• Clear and readable from a distance

```html
<!DOCTYPE html>
<html lang="en">
<head>
<meta charset="utf-8">
<title>Now Leasing Banner – Maplebrook Terrace</title>
<link rel="stylesheet" href="https://fonts.googleapis.com/css2?family=Libre+Caslon+Text:ital,wght@0,700;1,700&family=Yellowtail&family=Arimo:wght@700&display=swap">
<style>
  :root {
    --coral: #dc5052;
    --sun: #f9e033;
    --ink: #111111;
    --paper: #ffffff;
    --stage: #111111;
  }
  html, body {
    margin: 0;
    width: 1200px;
    height: 469px;
    overflow: hidden;
    background: var(--stage);
  }
  .canvas {
    position: relative;
    width: 1200px;
    height: 469px;
  }
  .banner {
    position: absolute;
    width: 1120px;
    height: 149px;
    display: block;
  }
  .banner--coral { left: 42px; top: 55px; }
  .banner--paper { left: 40px; top: 253px; }
  .now {
    font-family: "Yellowtail", "Brush Script MT", cursive;
    font-style: italic;
    font-size: 78px;
  }
  .leasing { font-family: "Libre Caslon Text", Georgia, serif; font-weight: 700; font-size: 108px; }
  .property-name { font-family: "Libre Caslon Text", Georgia, serif; font-weight: 700; font-size: 38px; }
  .phone { font-family: "Arimo", Arial, sans-serif; font-weight: 700; font-size: 36px; }

  .banner--coral .field-main { fill: var(--coral); }
  .banner--coral .field-side { fill: var(--paper); }
  .banner--coral .now { fill: var(--paper); }
  .banner--coral .leasing { fill: var(--sun); }
  .banner--coral .property-name { fill: var(--ink); }
  .banner--coral .phone { fill: var(--coral); }

  .banner--paper .field-main { fill: var(--paper); }
  .banner--paper .field-side { fill: var(--coral); }
  .banner--paper .now { fill: var(--ink); }
  .banner--paper .leasing { fill: var(--coral); }
  .banner--paper .property-name { fill: var(--paper); }
  .banner--paper .phone { fill: var(--paper); }
</style>
</head>
<body>
<main class="canvas">
  <svg class="banner banner--coral" viewBox="0 0 1120 149" aria-label="Now Leasing, Maplebrook Terrace, 925-318-6042">
    <rect class="field-side" width="1120" height="149"/>
    <path class="field-main" d="M0 0 H674 C700 0 716 26 704 50 L655 149 H0 Z"/>
    <text class="now" x="28" y="100" textLength="92" lengthAdjust="spacingAndGlyphs">Now</text>
    <text class="leasing" x="134" y="113" textLength="518" lengthAdjust="spacingAndGlyphs">LEASING</text>
    <text class="property-name" x="734" y="70" textLength="320" lengthAdjust="spacingAndGlyphs">Maplebrook Terrace</text>
    <text class="phone" x="733" y="121" textLength="202" lengthAdjust="spacingAndGlyphs">925-318-6042</text>
  </svg>

  <svg class="banner banner--paper" viewBox="0 0 1120 149" aria-label="Now Leasing, Maplebrook Terrace, 925-318-6042">
    <rect class="field-side" width="1120" height="149"/>
    <path class="field-main" d="M0 0 H674 C700 0 716 26 704 50 L655 149 H0 Z"/>
    <text class="now" x="28" y="100" textLength="92" lengthAdjust="spacingAndGlyphs">Now</text>
    <text class="leasing" x="134" y="113" textLength="518" lengthAdjust="spacingAndGlyphs">LEASING</text>
    <text class="property-name" x="734" y="70" textLength="320" lengthAdjust="spacingAndGlyphs">Maplebrook Terrace</text>
    <text class="phone" x="733" y="121" textLength="202" lengthAdjust="spacingAndGlyphs">925-318-6042</text>
  </svg>
</main>
</body>
</html>
```